Black Car Limousine transportation business in Naples Florida

Always stand for my reliability and RVD stands for Love, K and M are the first initials of my children's names. It should show professionalism and a dedication to customer service. We keep our clients identities private. Show our professionalism. We are Black car Black tie company. We service transportation on a reserve basis to and from residents, airports, casinos, hotels,

Target Market(s)

It is a Private car service. High end clients. Businesses, Celebrity and athletes. Service to airports, hotels, special events.

Industry/Entity Type

Business

Contact Information for Business Card

A pearl metallic or Luster card. Standard business card size. Would like the name, Company email, show we take credit cards and phone number. Currently I don't have a website but will like to add later.

Logo Text

STEADFAST RVD TRANSPORTATION

Font styles to use
Serif

Colors
eaeaea
000000

Requirements
Must have
• Must have Company email, show we take credit cards and phone number. Currently I don't have a website but will like to add later.
Nice to have
• Would like to stay with a black and white theme. Open to some color trim.
Should not have
• Open to suggestions

```html
<!DOCTYPE html>
<html lang="en">
<head>
<meta charset="utf-8">
<title>Steadfast RVD Transportation – Business Card</title>
<link rel="stylesheet" href="https://fonts.googleapis.com/css2?family=Open+Sans:ital,wght@0,400;0,600;1,700&display=swap">
<style>
  :root {
    --backdrop: #b3b3b3;
    --card-white: #ffffff;
    --card-grey: #8a8a8a;
    --ink: #000000;
    --ink-soft: #3a3a3a;
    --logo-grey: #8c8c8c;
    --divider: #c8c8c8;
    --wave-grey: #9a9a9a;
    --vehicle-dark: #2a2a2a;
    --vehicle-light: #6a6a6a;
  }
  * { margin: 0; padding: 0; box-sizing: border-box; }
  html, body {
    width: 1105px; height: 1200px; overflow: hidden;
    background: var(--backdrop);
    font-family: "Open Sans", Arial, sans-serif;
  }
  .card {
    position: absolute; left: 193px; width: 720px; height: 410px; overflow: hidden;
    box-shadow: 0 3px 8px rgba(0,0,0,.35);
  }
  .card--front { top: 167px; background: var(--card-white); }
  .card--back { top: 621px; background: var(--card-grey); }

  .vehicle-photo {
    position: absolute; border-radius: 14px 22px 6px 6px;
    background: linear-gradient(180deg, var(--vehicle-light), var(--vehicle-dark) 55%, #111);
  }
  .card--front .vehicle-photo { left: 59px; top: 197px; width: 125px; height: 50px; }
  .card--back .vehicle-photo { left: 121px; top: 182px; width: 176px; height: 70px; }

  .wordmark {
    position: absolute; font-weight: 600; line-height: 1; text-align: left;
  }
  .wordmark span { display: block; }
  .card--front .wordmark { left: 194px; top: 170px; color: var(--logo-grey); }
  .card--front .wordmark .wm-top { font-size: 15px; letter-spacing: 2px; }
  .card--front .wordmark .wm-main { font-size: 50px; letter-spacing: 2px; margin-top: 2px; }
  .card--front .wordmark .wm-sub { font-size: 10.5px; letter-spacing: 2.6px; margin-top: 2px; }
  .card--back .wordmark { left: 312px; top: 135px; color: var(--ink); }
  .card--back .wordmark .wm-top { font-size: 21px; letter-spacing: 3px; }
  .card--back .wordmark .wm-main { font-size: 70px; letter-spacing: 3px; margin-top: 2px; }
  .card--back .wordmark .wm-sub { font-size: 15px; letter-spacing: 3.6px; margin-top: 2px; }

  .divider {
    position: absolute; left: 400px; top: 126px; width: 1px; height: 156px; background: var(--divider);
  }
  .contact-block { position: absolute; left: 432px; top: 128px; color: var(--ink); }
  .contact-name { font-size: 25px; font-weight: 600; letter-spacing: .3px; line-height: 1.2; }
  .contact-role { font-size: 18px; color: var(--ink-soft); line-height: 1.2; margin-bottom: 18px; }
  .contact-list { list-style: none; }
  .contact-list li {
    display: flex; align-items: center; gap: 12px;
    font-size: 18px; color: var(--ink-soft); height: 27.5px;
  }
  .contact-list svg { width: 17px; height: 17px; fill: var(--ink); flex: none; }

  .wave { position: absolute; left: 0; bottom: 0; width: 720px; height: 90px; }

  .payment-note {
    position: absolute; left: 0; right: 0; top: 335px;
    display: flex; justify-content: center; align-items: center; gap: 10px;
    font-size: 17px; font-weight: 700; font-style: italic; color: var(--ink);
  }
  .payment-note svg { width: 30px; height: 20px; }
</style>
</head>
<body>

<section class="card card--front" aria-label="Business card front">
  <div class="vehicle-photo" role="img" aria-label="Photo of a black luxury SUV"></div>
  <div class="wordmark" aria-label="Steadfast RVD Transportation">
    <span class="wm-top">STEADFAST</span>
    <span class="wm-main">RVD</span>
    <span class="wm-sub">TRANSPORTATION</span>
  </div>

  <div class="divider"></div>

  <div class="contact-block">
    <p class="contact-name">DANIEL REYES</p>
    <p class="contact-role">CEO/Founder</p>
    <ul class="contact-list">
      <li>
        <svg viewBox="0 0 24 24" aria-hidden="true"><path d="M6.6 10.8a15.1 15.1 0 0 0 6.6 6.6l2.2-2.2c.3-.3.7-.4 1-.2 1.1.4 2.3.6 3.6.6.6 0 1 .4 1 1V20c0 .6-.4 1-1 1A17 17 0 0 1 3 4c0-.6.4-1 1-1h3.5c.6 0 1 .4 1 1 0 1.3.2 2.5.6 3.6.1.3 0 .7-.2 1z"/></svg>
        239 555 0187
      </li>
      <li>
        <svg viewBox="0 0 24 24" aria-hidden="true"><path d="M2 5h20v14H2z M2 5l10 8 10-8" fill="none" stroke="#000" stroke-width="0"/><path d="M2 5h20v2l-10 7L2 7z"/><path d="M2 9l10 7 10-7v10H2z"/></svg>
        ride@steadfastrvd.com
      </li>
      <li>
        <svg viewBox="0 0 24 24" aria-hidden="true"><circle cx="12" cy="12" r="10"/><path d="M7 6c2 1 3 3 2 5s1 3 2 4-1 4-1 4M15 4c-1 2 1 3 2 4s2 3 4 3" fill="none" stroke="#fff" stroke-width="1.6"/></svg>
        www.steadfastrvd.com
      </li>
    </ul>
  </div>

  <svg class="wave" viewBox="0 0 720 90" preserveAspectRatio="none" aria-hidden="true">
    <path d="M0 0 C120 22 260 28 420 12 C540 0 640 8 720 30 L720 90 L0 90 Z" fill="var(--wave-grey)"/>
    <path d="M0 35 C150 50 300 30 430 22 C560 14 660 24 720 40 L720 90 L0 90 Z" fill="var(--card-white)"/>
    <path d="M0 40 C150 55 300 36 430 28 C560 20 660 30 720 46 L720 90 L0 90 Z" fill="var(--ink)"/>
  </svg>
</section>

<section class="card card--back" aria-label="Business card back">
  <div class="vehicle-photo" role="img" aria-label="Photo of a black luxury SUV"></div>
  <div class="wordmark" aria-label="Steadfast RVD Transportation">
    <span class="wm-top">STEADFAST</span>
    <span class="wm-main">RVD</span>
    <span class="wm-sub">TRANSPORTATION</span>
  </div>

  <p class="payment-note">
    <svg viewBox="0 0 30 20" aria-hidden="true"><rect x="1" y="1" width="28" height="18" rx="3" fill="var(--ink)"/><rect x="1" y="5" width="28" height="3" fill="var(--card-grey)"/></svg>
    We accept credit cards
  </p>
</section>

</body>
</html>
```